Recruitment of Trellan Staffing for the UK market

I want a website for the UK market to attract businesses and companies to come to us for Philipine labour. We want an information site that gives all information on what we do and how we can recruit Philippine labour.
This is a recruitment site for companies to contact us with their requirements for skilled workers coming from the Philipines over to the UK to work.

Target Market(s)

Uk Companies and businesses who want Philipine skilled workers

Industry/Entity Type

REcruitment

Coding

Number of Pages Required

5+ page

Font styles to use
Sans Serif

Colors
0054AA
0677BA
7BADD7
CADEEF
E8F1F8
0094D4
00A9DD
6FCCEA
C7EBF8
E9F6FB
EE7325
F08F49
F5BC92
FAE3D3
FDF4ED
EB3D1F
EC4F4E
F09395
F8D3D4
FCEDEE

Requirements
Must have
• Look professional and corperate with drop down menus for Home ,about, services,articles. training , contact us
Nice to have
• Look at Velmora recruitment- https://velmorarecruitment.example.co.uk/. This is my current site - https://www.trellanstaffing.example.com/
Should not have
• Cartoons or silly pictures , needs to be corperate looking

```html
<!DOCTYPE html>
<html lang="en">
<head>
<meta charset="utf-8">
<title>Trellan Staffing — Skilled Philippine Workers for UK Companies</title>
<link rel="stylesheet" href="https://fonts.googleapis.com/css2?family=Outfit:wght@300;400;500;600&family=Oswald:wght@500;600&display=swap">
<style>
:root{
  --blue:#0054AA;
  --blue-dark:#0a4da0;
  --red:#EB3D1F;
  --orange:#EE7325;
  --ink:#1b1b1b;
  --text:#333;
  --muted:#555;
  --line:#d9d9d9;
  --soft:#f6f6f6;
  --maroon:#8b2b2b;
}
*{margin:0;padding:0;box-sizing:border-box}
html,body{width:1200px;height:3963px;overflow:hidden}
body{position:relative;font-family:"Outfit",sans-serif;color:var(--text);background:#fff}
.abs{position:absolute}
.btn{position:absolute;display:flex;align-items:center;justify-content:center;background:var(--blue);color:#fff;font-size:13px;font-weight:500;text-decoration:none}
.rule{display:block;width:42px;height:3px;background:var(--orange);margin-top:14px}
h2.section-title{font-family:"Outfit",sans-serif;font-weight:500;font-size:32px;color:var(--ink)}
.para{font-size:13.5px;line-height:23px;color:var(--text)}

/* header */
.site-header{position:absolute;left:0;top:0;width:1200px;height:75px;background:#fff}
.brand{position:absolute;left:162px;top:20px;font-family:"Outfit",sans-serif;font-weight:600;font-size:30px;color:var(--maroon);letter-spacing:.5px}
.header-contact{position:absolute;top:27px;font-size:15px;color:var(--muted);display:flex;align-items:center;gap:8px}
.menu-btn{position:absolute;left:997px;top:16px;width:43px;height:42px;background:var(--red);display:flex;align-items:center;justify-content:center}

/* hero */
.hero{position:absolute;left:0;top:75px;width:1200px;height:589px;background:linear-gradient(100deg,#3a4150 0%,#4e5868 35%,#6a7585 60%,#3d4656 100%)}
.hero-title{position:absolute;left:162px;top:305px;font-family:"Oswald",sans-serif;font-weight:500;font-size:39px;line-height:49px;color:#fff}
.hero-title span{color:var(--red)}
.contact-card{position:absolute;left:686px;top:257px;width:352px;height:463px;background:#fff;box-shadow:0 12px 30px rgba(0,0,0,.12)}
.contact-card h3{font-family:"Oswald",sans-serif;font-weight:500;font-size:31px;color:var(--red);text-align:center;margin-top:37px}
.field{position:absolute;left:32px;width:288px;height:36px;border:1px solid #888;font-size:13px;color:#666;padding:10px 0 0 34px}
.field svg{position:absolute;left:14px;top:12px}
.send{position:absolute;left:109px;top:375px;width:136px;height:36px;background:var(--red);color:#fff;font-size:14px;display:flex;align-items:center;justify-content:center}

/* about */
.about{position:absolute;left:0;top:820px;width:1200px;text-align:center}
.about h2{font-size:32px;font-weight:500;color:var(--ink)}
.about .rule{margin:12px auto 0}
.about p{width:740px;margin:18px auto 0;font-size:12.5px;line-height:23px}

.map{position:absolute;left:631px;top:1061px;width:392px;height:377px;background:radial-gradient(ellipse at 60% 50%,#e9eef3 0%,#f5f7f9 55%,#fff 80%)}
.photo-circle{position:absolute;width:358px;height:358px;border-radius:50%}

/* service cards */
.services{position:absolute;left:0;top:2764px;width:1200px;height:454px;background:var(--soft)}
.card{position:absolute;top:126px;width:269px;height:237px;background:#fff;border:1px solid var(--line);text-align:center}
.card .icon{position:absolute;left:102px;top:-37px;width:65px;height:65px;border-radius:50%;background:#fff;border:1px solid var(--line);display:flex;align-items:center;justify-content:center}
.card h3{margin-top:53px;font-size:17px;font-weight:500;color:var(--ink)}
.card p{margin:14px auto 0;width:230px;font-size:12px;line-height:23px}
.card .btn{left:78px;top:173px;width:113px;height:37px}

/* contact band */
.cta{position:absolute;left:0;top:3218px;width:1200px;height:450px;background:linear-gradient(90deg,#1a1d22 0%,#26292f 45%,#3c3f46 70%,#1d2026 100%)}
.cta h2{position:absolute;left:162px;top:93px;font-size:33px;font-weight:500;color:#fff}
.cta p{position:absolute;left:162px;width:420px;font-size:12.5px;line-height:23px;color:#fff}
.cta .btn-light{position:absolute;left:162px;top:315px;width:112px;height:36px;background:#fff;color:var(--blue);font-size:13px;font-weight:500;display:flex;align-items:center;justify-content:center}

/* footer */
.site-footer{position:absolute;left:0;top:3668px;width:1200px;height:249px;background:#fff}
.site-footer h4{position:absolute;top:50px;font-size:15px;font-weight:500;color:var(--ink)}
.site-footer h4::after{content:"";display:block;width:32px;height:2px;background:var(--orange);margin-top:10px}
.qlink{position:absolute;font-size:13px;color:#444}
.qlink::before{content:"›";margin-right:9px;font-size:15px}
.fdetail{position:absolute;left:469px;font-size:13px;line-height:20px;color:#444}
.social{position:absolute;top:105px;width:28px;height:28px;border-radius:50%;border:1px solid #b8c7e0}
.footer-brand{position:absolute;left:800px;top:160px;font-size:24px;font-weight:600;color:var(--maroon)}
.legal{position:absolute;left:0;top:3917px;width:1200px;height:46px;background:var(--blue);color:#fff;font-size:12.5px;display:flex;align-items:center;justify-content:center}
</style>
</head>
<body>

<header class="site-header">
  <div class="brand">Trellan Staffing</div>
  <div class="header-contact" style="left:608px">
    <svg width="16" height="16" viewBox="0 0 24 24" fill="none" stroke="#EB3D1F" stroke-width="2"><path d="M5 3h4l2 5-3 2a12 12 0 0 0 6 6l2-3 5 2v4a2 2 0 0 1-2 2A17 17 0 0 1 3 5a2 2 0 0 1 2-2z"/></svg>
    07700 900412
  </div>
  <div class="header-contact" style="left:749px;font-size:13px">
    <svg width="17" height="13" viewBox="0 0 24 18" fill="none" stroke="#EB3D1F" stroke-width="2"><rect x="1" y="1" width="22" height="16"/><path d="M1 1l11 9 11-9"/></svg>
    sales@trellanstaffing.example.com
  </div>
  <div class="menu-btn"><svg width="18" height="14" viewBox="0 0 18 14" stroke="#fff" stroke-width="1.6"><path d="M0 2h18M3 7h12M6 12h6"/></svg></div>
</header>

<section class="hero" role="img" aria-label="Photo of two engineers in hard hats discussing work in a warehouse">
</section>
<h1 class="hero-title">Recruiting and Placing Skilled<br>Philippine Workers into<br><span>UK Companies</span></h1>

<form class="contact-card">
  <h3>Contact Us Today</h3>
  <div class="field" style="top:121px"><svg width="11" height="12" viewBox="0 0 11 12" fill="#333"><circle cx="5.5" cy="3" r="3"/><path d="M0 12a5.5 5 0 0 1 11 0z"/></svg>Name</div>
  <div class="field" style="top:166px"><svg width="12" height="9" viewBox="0 0 12 9" fill="#333"><rect width="12" height="9"/><path d="M0 0l6 5 6-5" stroke="#fff" fill="none"/></svg>Email</div>
  <div class="field" style="top:212px"><svg width="11" height="11" viewBox="0 0 24 24" fill="#333"><path d="M5 2h4l2 5-3 2a12 12 0 0 0 6 6l2-3 5 2v4a2 2 0 0 1-2 2A17 17 0 0 1 3 4a2 2 0 0 1 2-2z"/></svg>Phone</div>
  <div class="field" style="top:257px;height:98px"><svg width="11" height="10" viewBox="0 0 11 10" stroke="#333" stroke-width="1.6"><path d="M0 1h11M0 4h11M0 7h11M0 10h7"/></svg>Message</div>
  <div class="send">Send Message</div>
</form>

<section class="about">
  <h2>What The Business is About</h2>
  <span class="rule"></span>
  <p>We source skilled workers directly from the Philippines to work in the UK. With offices , training locations and specialist recruiters we can find the highest quality individuals to add value and resources to any UK buisness. We delivery quality based on vast experience over a number of years.</p>
</section>
<a class="btn" style="left:543px;top:969px;width:112px;height:36px">Contact Us</a>

<section>
  <h2 class="section-title abs" style="left:162px;top:1133px">Working Together<span class="rule"></span></h2>
  <p class="abs" style="left:162px;top:1202px;font-size:17px;line-height:34px;color:#222;width:400px">We recruit the finest talent available with our dedicated 200 strong team.<br>Our centres are highlighted in <b style="color:var(--red);text-decoration:underline">Red Dots</b> on the map.</p>
  <a class="btn" style="left:162px;top:1349px;width:112px;height:37px">Contact Us</a>
  <div class="map" role="img" aria-label="Map of the Philippines with centres marked at Baguio, Manila, Batangas, Bacolod and Davao"></div>
</section>

<section>
  <div class="photo-circle" style="left:162px;top:1526px;background:radial-gradient(circle at 50% 45%,#dde3ea,#8a9aae 70%,#5d6d82)" role="img" aria-label="Photo of two businessmen reviewing work at a laptop with UK and Philippine flags"></div>
  <h2 class="section-title abs" style="left:600px;top:1600px">What We Do<span class="rule"></span></h2>
  <p class="abs para" style="left:600px;top:1670px;width:440px;font-size:12.5px">Our company has been estabilished in the Philippines for over 20 years. We have mainly been recruiting philippine workers for the off shore industry in asia but since brexit and the new rules on skilled workers entering the UK we have been working with UK companies who now have chance to recruit some of the finest hard working talent from the Philippines for their companies..</p>
</section>

<section>
  <h2 class="section-title abs" style="left:162px;top:2007px">How We Help<span class="rule"></span></h2>
  <p class="abs para" style="left:162px;top:2076px;width:440px;font-size:12.5px">We work with companies to find skilled workers that meet the UK requirements for Visas and work permits. We guide you through the whole process and deliver highly trained people that add value to your business. We are here to help both the companies and the Philippino people to gain a better standard of living for their families.</p>
  <div class="photo-circle" style="left:680px;top:1921px;background:radial-gradient(circle at 60% 45%,#c9d84a,#5e6a55 60%,#2f3530)" role="img" aria-label="Photo of a machinist in a hi-vis vest and helmet working at a lathe"></div>
</section>

<section>
  <div class="photo-circle" style="left:162px;top:2318px;background:radial-gradient(circle at 50% 55%,#e59a4a,#9a8a70 55%,#5f5548)" role="img" aria-label="Photo of two site engineers in orange vests and hard hats holding a tablet"></div>
  <h2 class="section-title abs" style="left:600px;top:2362px">Where To Start<span class="rule"></span></h2>
  <p class="abs para" style="left:600px;top:2431px;width:440px;font-size:12.5px">We need to know what your issues are and how we can understand the personnal you require , over what time frame and the number of employees you need. Once this is estabilished we start sourcing workers in the Philippines that meet your criteria while starting the process in the UK to be able to have all the documents in place to deliver your company hard working skilled individuals.</p>
  <a class="btn" style="left:600px;top:2585px;width:112px;height:37px">Contact Us</a>
</section>

<section class="services">
  <article class="card" style="left:162px">
    <div class="icon"><svg width="34" height="34" viewBox="0 0 34 34" fill="none" stroke="#0054AA" stroke-width="1.5"><rect x="6" y="5" width="20" height="26"/><path d="M12 3h8v5h-8zM10 14h2M15 14h8M10 20h2M15 20h8M10 26h2M15 26h6"/></svg></div>
    <h3>UK Skilled Workers List</h3>
    <p>The UK government since brexit have developed a new system based on points (similar to Australia)...</p>
    <a class="btn">Read More</a>
  </article>
  <article class="card" style="left:465px">
    <div class="icon"><svg width="34" height="34" viewBox="0 0 34 34" fill="none" stroke="#0054AA" stroke-width="1.5"><rect x="7" y="4" width="20" height="27"/><circle cx="13" cy="11" r="3"/><path d="M18 10h6M18 13h6M11 19h13M11 23h13M11 27h8"/></svg></div>
    <h3>Sponsor Licence</h3>
    <p>If you have areas of your business that meet the entry requirements of skilled labour your next...</p>
    <a class="btn">Read More</a>
  </article>
  <article class="card" style="left:769px">
    <div class="icon"><svg width="34" height="34" viewBox="0 0 34 34" fill="none" stroke="#0054AA" stroke-width="1.5"><circle cx="22" cy="21" r="8"/><path d="M22 16v5l3 2M5 30h12M8 30V18h6v12M11 18v-6"/><circle cx="11" cy="8" r="3"/></svg></div>
    <h3>Recruitment Timeline</h3>
    <p>Brief us on the job profiles – this is passed on to our teams in the Philippines...</p>
    <a class="btn">Read More</a>
  </article>
</section>

<section class="cta" role="img" aria-label="Photo of two smiling engineers in hard hats and work jackets holding a laptop">
</section>
<div class="abs" style="left:0;top:3218px;width:1200px;height:450px">
  <h2 class="abs" style="left:162px;top:93px;font-size:33px;font-weight:500;color:#fff">Contact Us Today</h2>
  <p class="abs" style="left:162px;top:162px;width:430px;font-size:12.5px;line-height:23px;color:#fff">Please contact us today with your requirements, this can be care workers, chef, welders, pipe fitters, caravan cabinet makers, medical workers. The UK list of required skills is extensive &amp; the Philippines offersenglish speaking highly qualified hard working employees.</p>
  <p class="abs" style="left:162px;top:254px;width:430px;font-size:12.5px;line-height:23px;color:#fff;font-weight:500">Contact us today and make that first step to a highly motivated , quality skilled workforce.</p>
  <div class="btn-light abs" style="left:162px;top:315px;width:112px;height:36px;background:#fff;color:var(--blue);font-size:13px;font-weight:500;display:flex;align-items:center;justify-content:center">Contact Us</div>
</div>

<footer class="site-footer">
  <h4 style="left:162px">Quick Links</h4>
  <span class="qlink" style="left:162px;top:99px">Home</span>
  <span class="qlink" style="left:267px;top:99px">Articles</span>
  <span class="qlink" style="left:162px;top:141px">About</span>
  <span class="qlink" style="left:267px;top:141px">Training</span>
  <span class="qlink" style="left:162px;top:182px">Services</span>
  <span class="qlink" style="left:267px;top:182px">Contact Us</span>

  <h4 style="left:440px">Contact Details</h4>
  <svg class="abs" style="left:440px;top:103px" width="14" height="19" viewBox="0 0 14 19" fill="#0054AA"><path d="M7 0a7 7 0 0 1 7 7c0 5-7 12-7 12S0 12 0 7a7 7 0 0 1 7-7z"/><circle cx="7" cy="7" r="2.5" fill="#fff"/></svg>
  <p class="fdetail" style="top:101px">4 Linden Court, Seaholme<br>HU99 1ZZ United Kingdom</p>
  <svg class="abs" style="left:440px;top:152px" width="16" height="16" viewBox="0 0 24 24" fill="none" stroke="#0054AA" stroke-width="2"><path d="M5 3h4l2 5-3 2a12 12 0 0 0 6 6l2-3 5 2v4a2 2 0 0 1-2 2A17 17 0 0 1 3 5a2 2 0 0 1 2-2z"/></svg>
  <p class="fdetail" style="top:150px">07700 900412</p>
  <svg class="abs" style="left:439px;top:185px" width="18" height="13" viewBox="0 0 18 13" fill="#0054AA"><rect width="18" height="13"/><path d="M0 0l9 7 9-7" stroke="#fff" fill="none"/></svg>
  <p class="fdetail" style="top:180px">sales@trellanstaffing.example.com</p>

  <h4 style="left:800px">Follow Us On</h4>
  <span class="social" style="left:800px"></span>
  <span class="social" style="left:835px"></span>
  <span class="social" style="left:870px"></span>
  <span class="social" style="left:905px"></span>
  <div class="footer-brand">Trellan Staffing</div>
</footer>
<div class="legal">© 2023 Trellan Staffing Ltd. All Rights Reserved</div>

</body>
</html>
```